Garlic Farm for Farm Sales/Restaurant sales

Need a professional, but appealing to agriculture world. We are selling 27 kinds of Organic Garlic from a farm in Simla,CO. I have uploaded logo and business information-we are going to need a template, because I will need to use it for four separate people.
-We are trying to appeal to Farm to table restaurants
-As well as growers/farmers

Target Market(s)

Agriculture Sales/Restaurants-Organic

Industry/Entity Type

Agriculture

Contact Information for Business Card

Want it to look more unique then your average kelto stock card- I want it to look amazing

Font styles to use
Sans Serif

Colors
0455a3
ec1f27
fbed22
ffffff

Requirements
Must have
• Just be creative
Nice to have
• Colorful
Should not have
• plain

```html
<!DOCTYPE html>
<html lang="en">
<head>
<meta charset="utf-8">
<title>Highplain Garlic – Business Card</title>
<link href="https://fonts.googleapis.com/css2?family=Open+Sans:ital,wght@0,400;0,700;1,400;1,700&display=swap" rel="stylesheet">
<style>
  :root {
    --navy: #062c5f;
    --red: #d8262e;
    --paper: #f4f4f4;
    --white: #ffffff;
    --backdrop: #e7e4e2;
  }
  * { box-sizing: border-box; margin: 0; padding: 0; }
  html, body { width: 1200px; height: 900px; overflow: hidden; }
  body {
    background: var(--backdrop);
    font-family: "Open Sans", Arial, sans-serif;
    position: relative;
  }
  .card {
    position: absolute;
    background: var(--paper);
    box-shadow: 0 6px 18px rgba(0,0,0,0.18);
    overflow: hidden;
  }
  .card-front { left: 240px; top: 60px; width: 556px; height: 345px; }
  .card-back { left: 457px; top: 518px; width: 560px; height: 344px; }

  .front-header {
    height: 132px;
    display: flex;
    align-items: center;
    justify-content: center;
    padding-left: 10px;
  }
  .brand-name {
    color: var(--navy);
    font-weight: 700;
    font-size: 34px;
    letter-spacing: 0.5px;
    white-space: nowrap;
  }
  .front-body {
    position: absolute;
    left: 0; top: 132px; right: 0; bottom: 0;
    background: var(--navy);
    color: var(--white);
  }
  .person-name {
    position: absolute; left: 30px; top: 10px;
    font-weight: 700; font-style: italic; font-size: 28px;
  }
  .person-role {
    position: absolute; left: 28px; top: 50px;
    font-style: italic; font-size: 18px;
  }
  .contact-list {
    position: absolute; left: 28px; top: 97px;
    list-style: none; font-size: 15px; line-height: 21px;
  }
  .contact-list li { display: flex; align-items: center; gap: 6px; }
  .contact-list svg { width: 14px; height: 14px; fill: var(--white); }
  .postal-address {
    position: absolute; right: 30px; top: 138px;
    text-align: right; font-size: 15px; line-height: 21px; font-style: normal;
  }

  .back-mark {
    position: absolute; left: 233px; top: 82px;
    width: 96px; height: 96px; border-radius: 50%;
    background: var(--red);
  }
  .back-name {
    position: absolute; left: 0; right: 0; top: 190px;
    text-align: center;
  }
</style>
</head>
<body>
  <section class="card card-front">
    <header class="front-header">
      <span class="brand-name">Highplain Garlic</span>
    </header>
    <div class="front-body">
      <div class="person-name">dale marsh</div>
      <div class="person-role">Owner</div>
      <ul class="contact-list">
        <li><svg viewBox="0 0 16 16" aria-hidden="true"><path d="M1 6c0-3 14-3 14 0v2h-4V6.5c-2-.7-4-.7-6 0V8H1zM4 9h8l2 5H2z"/></svg>555-014-2238</li>
        <li><svg viewBox="0 0 16 16" aria-hidden="true"><path d="M2 5h2V1h8v4h2v10H2zM5 2v3h6V2zM4 8h2v2H4zm3 0h2v2H7zm3 0h2v2h-2zM4 11h2v2H4zm3 0h2v2H7zm3 0h2v2h-2z"/></svg>(555)-016-4</li>
        <li><svg viewBox="0 0 16 16" aria-hidden="true"><path d="M1 3h14v10H1zm1.5 1.2L8 8.5l5.5-4.3z"/></svg>hello@highplain.com</li>
        <li><svg viewBox="0 0 16 16" aria-hidden="true"><circle cx="8" cy="8" r="7"/></svg>www.highplaingarlic.com</li>
      </ul>
      <address class="postal-address">PO Box 20417,<br>Harlow, CO 80812</address>
    </div>
  </section>

  <section class="card card-back">
    <span class="back-mark" aria-hidden="true"></span>
    <div class="back-name"><span class="brand-name">Highplain Garlic</span></div>
  </section>
</body>
</html>
```